Website development company website

ABOUT COMPANY
Hi everyone! We're a Melbourne, Australia website development company in a need of a website design that will make online store merchants want to engage our services.
We specialise exclusively in Torvista e-commerce platform (https://torvista-platform.example/). What distinguishes our business from competition is that rather than designing and building brand new websites, we offer development, support and maintenance services to established websites. Maintenance and Support are the keywords representing our business.
Our potential clients are people with broken, slow and underperforming Torvista installations who need assistance getting their websites up and making sales. Our website must pass the message that we can help, and provide quick means of making contact.
DESIGN
Overall, we're looking for a slick, clean, airy, conservative design. No need to do anything crazy, try to stick to what's "standard" in website design these days and make it easy on all of us. The website is unlikely to be updated too often so it needs to look attractive and fresh first time over and after a year, too.
Attached is our new logo, which you'll be able to take the basic idea from, the colors and fonts. Though, don't use the fonts from the logo in the website, stick to the standard widely supported fonts. Additional use of Google fonts is fine.
Don't overdo it with colors, stick to conservative basic color set and only use the colors from the log for accents like headings etc. Please, don't be tempted to use the blue and orange as background of whole blocks, other than perhaps footer. Thanks.
For the images used, I'd like to stay away from a design studio/digital agency feel and lean more towards professional support and maintenance services. I'm thinking images of content merchants doing their job. Something along the lines of "We'll be taking care of the website so that you only need to care about the business".
Some ideas I like:
http://www.plumframe-pics.example/detail/photo/portrait-of-confident-male-design-professional-royalty-free-image/572048163
http://www.plumframe-pics.example/detail/photo/designer-taking-picture-of-hat-high-res-stock-photography/839207514
http://www.plumframe-pics.example/detail/photo/woman-packaging-pottery-royalty-free-image/216684093
Images of colorful shopping bags and shopping carts are over the top and not serious enough. Instead of images matching Online Shopping, I'd try going more for Stability, Reliability, Performance.
Our existing website is http://www.bravuln.example. Please, don't take design ideas from it, but it will give you a picture of the structure of our new website and content that's going to be used initially.
If you could include a basic icon set to use throughout the website, that would be great. If the icons could match our logo (attached), it would be a big plus.
ALL PAGES
Every page must contain clearly visible phone number (1300 648 907) and a Contact Us Now button, which opens an AJAX driven popup form with Name, Email, Phone and Message to be sent through.
To start with, main menu items will be Torvista, Portfolio, Contact.
At the bottom of each page, please, include a newsletter subscription form with text Subscribe to Torvista Support and Security Updates.
For the footer, I'd like to see a logo strip with the following logos in grayscale (no need to link anywhere): Torvista, QRX, DataVane, NCB. You'll find the logos on Google Images.
Standard footer columns follow. Here, I'd like to see logos in color: Torvista Certified Developer, Torvista Ceritified Solution Provider. Again, the logos are on Google Images.
No social media logos/links necessary anywhere on the website.
...and then the copyright line.
FRONT PAGE
Large slider with images that would appeal to our target audience. Keywords here would be Torvista System Audit, Torvista Performance Optimisation, Torvista Website Emergency Recovery, Torvista Development Infrastructure Hosting. We'll have a static page created for each of these to link to.
In a corner of the slider, or on the edge, can I have an overlay with logos in color (same as footer): Torvista Certified Developer, Torvista Ceritified Solution Provider.
Underneath, a number of blocks, each with an image and teaser that we'll use to link to various pages throughout the website.
PORTFOLIO PAGE
I'm thinking a single long page with a block per client, which will contain project name, description from us and a testimonial from client. Also, each block will contain a single large screenshot. No gallery or slideshow is necessary here, just one image per project.
I'll leave the layout up to you, but try to put yourself in the shoes of a potential client reviewing our past work by simply scrolling down this one page.
CONTACT US PAGE
Separate page with the same form as above, phone number (1300 648 907), email address (support@kavreo.example), address (Suite 42, Level 3|8 Wattlebrook Lane|Fernvale Heights VIC 3999), and a grayscale Area Map.
CODING UP
Coding up into static HTML/CSS/JS is equally important as the design itself. We're a website development company, we'll be integrating the theme. We will spot any issues and we will point them out.
Coded up design must be fully responsive. Enough said.
To be able to create any content in future, we'd like one extra page coded up with samples of all themed elements, lists, forms, buttons, 2, 3, 4-column layout, alerts, icons, etc. This page does not need to be designed, only coded up.
The design will be integrated into Drupal using Twig. If possible at all, try to keep it in mind when designing and coding up, and make the integration into a Drupal theme easier for us.
GOOD LUCK!
That's it. Let me know if anything needs clarifying. So far I've had a great experience with ArtFlockly. I don't doubt some great designs will emerge. Clever ideas are highly appreciated, but also make it clear you've read and followed the points in this brief. Cheers, Tom

```html
<!DOCTYPE html>
<html lang="en">
<head>
<meta charset="utf-8">
<title>Kavreo E-commerce — Torvista Development, Support and Maintenance</title>
<link rel="stylesheet" href="https://fonts.googleapis.com/css2?family=Open+Sans:wght@300;400;600;700&family=Arimo:wght@700&display=swap">
<style>
:root{
  --orange:#f07c1b;
  --navy:#1d4a7e;
  --ink:#333333;
  --muted:#777777;
  --strip:#ececec;
  --footer:#262626;
  --footer-base:#1c1c1c;
  --teal:#4cb8b1;
  --white:#ffffff;
  --line:#dddddd;
}
*{box-sizing:border-box;margin:0;padding:0}
html,body{width:1200px;height:2970px;overflow:hidden}
body{font-family:"Open Sans",Arial,sans-serif;color:var(--ink);background:var(--white);position:relative}
section,header,footer{position:relative;width:1200px}
a{color:inherit;text-decoration:none}

/* header */
.site-header{height:88px;background:var(--white);box-shadow:0 1px 4px rgba(0,0,0,.08);z-index:2}
.brand{position:absolute;left:132px;top:22px;display:flex;align-items:center;gap:10px}
.brand-mark{width:34px;height:40px;background:var(--navy)}
.brand-name{font-size:34px;font-weight:700;color:var(--orange);letter-spacing:-.5px}
.main-nav{position:absolute;left:408px;top:0;height:88px;display:flex;align-items:center}
.main-nav a{font-size:14px;color:var(--ink);padding:0 14px;position:relative;height:88px;line-height:92px}
.main-nav a+a::before{content:"";position:absolute;left:-2px;top:44px;width:4px;height:4px;border-radius:50%;background:#bbb}
.main-nav a.active{color:var(--navy)}
.main-nav a.active::after{content:"";position:absolute;left:0;right:0;bottom:0;height:3px;background:var(--navy)}
.call-box{position:absolute;left:900px;top:14px;height:60px;border-left:1px solid var(--line);text-align:right;width:170px}
.call-label{font-size:13px;color:var(--ink);margin-top:8px}
.call-number{font-size:22px;font-weight:700;color:var(--orange);line-height:30px;white-space:nowrap}

/* hero */
.hero{height:490px;overflow:hidden}
.hero-photo{position:absolute;inset:0;background:
  radial-gradient(ellipse 420px 200px at 900px 400px,rgba(220,226,232,.55),rgba(220,226,232,0)),
  radial-gradient(ellipse 500px 300px at 300px 360px,rgba(150,165,185,.45),rgba(150,165,185,0)),
  linear-gradient(180deg,#243347 0%,#2f4058 40%,#55657a 70%,#a7afb9 100%)}
.hero-title{position:absolute;top:157px;width:100%;text-align:center;font-family:"Arimo",Arial,sans-serif;font-weight:700;font-size:33px;line-height:52px;color:var(--white);letter-spacing:1px}
.hero-actions{position:absolute;top:282px;width:100%;display:flex;justify-content:center;gap:20px}
.btn{display:inline-block;font-size:14px;line-height:34px;height:36px;padding:0 26px}
.btn-primary{background:var(--navy);color:var(--white)}
.btn-outline{border:2px solid var(--white);color:var(--white);line-height:32px}
.slider-arrow{position:absolute;top:219px;width:52px;height:52px;background:rgba(0,0,0,.35);display:flex;align-items:center;justify-content:center}
.slider-arrow.prev{left:0}.slider-arrow.next{right:0}

/* tech strip */
.tech-strip{height:100px;background:var(--strip);display:flex;align-items:center;justify-content:space-between;padding:0 130px}
.tech-strip.plain{background:var(--white)}
.tech-name{font-size:30px;font-weight:600;color:#a8a8a8}

/* welcome */
.welcome{height:486px;text-align:center}
.eyebrow{position:absolute;top:30px;width:100%;font-size:14px;color:var(--ink)}
.welcome-heading{position:absolute;top:66px;width:100%;font-size:25px;font-weight:300;line-height:32px;color:var(--ink)}
.welcome-heading strong{font-weight:400}
.cert-col{position:absolute;top:170px;width:400px}
.cert-col.left{left:129px}.cert-col.right{left:671px}
.cert-icon{height:70px;display:flex;justify-content:center;align-items:flex-end}
.cert-title{margin-top:26px;font-size:18px;font-weight:600}
.cert-text{margin-top:16px;font-size:12px;line-height:20px;color:var(--muted)}
.welcome-divider{position:absolute;left:600px;top:172px;width:1px;height:215px;background:var(--line)}

/* services */
.services{height:510px;background:linear-gradient(135deg,#454545 0%,#353535 50%,#3f3f3f 100%);text-align:center;color:var(--white)}
.section-title{position:absolute;top:32px;width:100%;font-size:25px;font-weight:300}
.section-title strong{font-weight:400}
.section-sub{position:absolute;top:78px;width:100%;font-size:13px}
.services .section-sub{color:#aaaaaa}
.service-card{position:absolute;top:173px;width:292px;height:204px;background:var(--white);color:var(--ink)}
.service-card:nth-of-type(1){left:133px}
.service-card:nth-of-type(2){left:454px}
.service-card:nth-of-type(3){left:775px}
.service-icon{position:absolute;left:106px;top:-30px;width:80px;height:80px;border-radius:50%;background:var(--teal);display:flex;align-items:center;justify-content:center}
.service-icon.portrait{background:linear-gradient(180deg,#f4d6b8 0%,#f0c9a4 55%,#3a8fd6 100%)}
.service-name{margin-top:70px;font-size:18px;font-weight:600}
.service-text{margin:6px 22px 0;font-size:12px;line-height:20px;color:var(--muted)}
.btn-small{position:absolute;left:50%;transform:translateX(-50%);bottom:22px;background:#ececec;color:#aaa;font-size:11px;padding:0 16px;line-height:24px;white-space:nowrap}
.services-note{position:absolute;top:406px;width:100%;font-size:13px;color:#bbbbbb}
.btn-ghost{position:absolute;top:442px;left:518px;width:164px;height:36px;border:2px solid var(--white);color:var(--white);font-size:14px;line-height:32px;background:rgba(255,255,255,.05)}

/* testimonials */
.testimonials{height:310px;text-align:center}
.testimonials .section-title,.portfolio .section-title{color:var(--ink)}
.testimonials .section-title{top:30px}
.testimonials .section-sub{top:74px;color:var(--ink)}
.client-photo{position:absolute;left:133px;top:153px;width:110px;height:110px;border-radius:50%;background:
  radial-gradient(circle at 50% 38%,#d8b79c 0,#d8b79c 18%,rgba(216,183,156,0) 30%),
  linear-gradient(180deg,#d9dee4 0%,#b9c3cd 50%,#2f4a6b 72%,#23364f 100%)}
.quote-rule{position:absolute;left:282px;top:146px;width:1px;height:120px;background:var(--line)}
.quote{position:absolute;left:316px;top:150px;width:760px;text-align:left;font-size:14px;line-height:28px;color:var(--ink)}
.quote-author{position:absolute;left:316px;top:238px;font-size:14px;font-weight:700;color:var(--orange)}
.quote-author span{font-weight:400;color:var(--muted)}

/* portfolio */
.portfolio{height:505px;background:#ebebeb;text-align:center}
.portfolio .section-title{top:30px}
.portfolio .section-sub{top:74px;color:var(--ink)}
.project{position:absolute;top:135px;width:210px;height:242px;background:var(--white);box-shadow:0 1px 3px rgba(0,0,0,.15)}
.project:nth-of-type(1){left:133px}.project:nth-of-type(2){left:374px}.project:nth-of-type(3){left:616px}.project:nth-of-type(4){left:857px}
.project-shot{height:198px}
.shot-1{background:linear-gradient(180deg,#2f78bd 0%,#6aa1d2 35%,#dfe7ee 60%,#c9d3dc 100%)}
.shot-2{background:linear-gradient(180deg,#f4f4f4 0%,#e6e6e6 40%,#d9473f 62%,#f0f0f0 80%,#e2e2e2 100%)}
.shot-3{background:linear-gradient(180deg,#6fb9e2 0%,#bfe0f2 40%,#f6f6f6 65%,#ececec 100%)}
.shot-4{background:linear-gradient(180deg,#3c8fc8 0%,#7cc0e1 25%,#f3f6f8 45%,#e7edf0 100%)}
.project-name{font-size:14px;line-height:44px;color:var(--ink)}
.port-arrow{position:absolute;top:230px}
.port-arrow.prev{left:56px}.port-arrow.next{right:56px}
.btn-view{position:absolute;top:420px;left:518px;width:164px;height:36px;border:2px solid #999;color:var(--muted);font-size:14px;line-height:32px}

/* footer */
.site-footer{height:325px;background:var(--footer);color:#cccccc}
.footer-col{position:absolute;top:46px}
.footer-col h3{font-size:18px;font-weight:600;color:var(--white);margin-bottom:20px}
.col-links{left:132px}.col-news{left:287px;width:236px}.col-contact{left:563px;width:210px}
.col-links li{list-style:none;font-size:12px;line-height:27px}
.col-news p,.col-contact p{font-size:12px;line-height:20px}
.news-field{margin-top:18px;height:36px;background:#3c3c3c;display:flex;align-items:center;padding-left:10px;gap:10px;font-size:11px;color:#777}
.btn-submit{margin-top:12px;width:110px;height:36px;background:var(--orange);color:var(--white);font-size:14px;font-weight:600;text-align:center;line-height:36px}
.col-contact p+p{margin-top:8px}
.footer-map{position:absolute;left:795px;top:50px;width:275px;height:158px;background:linear-gradient(135deg,#d6d6d6,#b9b9b9)}
.map-link{position:absolute;left:795px;top:214px;font-size:12px;text-decoration:underline}
.footer-base{height:60px;background:var(--footer-base);color:#aaaaaa;font-size:12px;text-align:center;line-height:60px}
</style>
</head>
<body>

<header class="site-header">
  <a class="brand" href="#"><span class="brand-mark"></span><span class="brand-name">Kavreo</span></a>
  <nav class="main-nav">
    <a class="active" href="#">Home</a>
    <a href="#">About Us</a>
    <a href="#">Torvista</a>
    <a href="#">Our Portfolio</a>
    <a href="#">Contact Us</a>
  </nav>
  <div class="call-box">
    <div class="call-label">Call Us Now!</div>
    <div class="call-number">1300 648 907</div>
  </div>
</header>

<section class="hero">
  <div class="hero-photo" role="img" aria-label="Business professionals in suits at a desk with a laptop, papers and pen"></div>
  <h1 class="hero-title">HIGH PERFORMANCE TORVISTA SITES<br>ON TIME AND ON BUDGET.</h1>
  <div class="hero-actions">
    <a class="btn btn-primary" href="#">Read More</a>
    <a class="btn btn-outline" href="#">Contact Us</a>
  </div>
  <a class="slider-arrow prev" href="#" aria-label="Previous slide"><svg width="14" height="22" viewBox="0 0 14 22"><path d="M12 2 3 11l9 9" fill="none" stroke="#fff" stroke-width="3"/></svg></a>
  <a class="slider-arrow next" href="#" aria-label="Next slide"><svg width="14" height="22" viewBox="0 0 14 22"><path d="M2 2l9 9-9 9" fill="none" stroke="#fff" stroke-width="3"/></svg></a>
</section>

<section class="tech-strip">
  <span class="tech-name">Markupa</span><span class="tech-name">Torvista</span><span class="tech-name">Brewlang</span><span class="tech-name">QRX</span><span class="tech-name">NCB</span><span class="tech-name">DataVane</span>
</section>

<section class="welcome">
  <p class="eyebrow">Welcome to Kavreo E-commerce</p>
  <h2 class="welcome-heading">New generation websites by <strong>new generation designers.</strong><br>For new generation entrepreneurs..</h2>
  <div class="cert-col left">
    <div class="cert-icon"><svg width="64" height="54" viewBox="0 0 64 54" fill="none" stroke="#f07c1b" stroke-width="2.5"><rect x="4" y="4" width="56" height="36" rx="2"/><path d="M2 46h60M24 16l-6 6 6 6M40 16l6 6-6 6M34 13l-4 18"/></svg></div>
    <h3 class="cert-title">Torvista Certified Developer</h3>
    <p class="cert-text">It is a long established fact that a reader will be distracted by the readable content of a page when looking at its layout. The point of using Lorem Ipsum is that it has a more-or-less normal distribution of letters, as opposed to using , making it look like readable English.</p>
  </div>
  <div class="welcome-divider"></div>
  <div class="cert-col right">
    <div class="cert-icon"><svg width="64" height="66" viewBox="0 0 64 66" fill="none" stroke="#f07c1b" stroke-width="2.5"><path d="M32 14a14 14 0 0 0-8 25v7h16v-7a14 14 0 0 0-8-25zM26 52h12M28 57h8M32 2v6M10 10l4 4M54 10l-4 4M2 28h6M56 28h6"/></svg></div>
    <h3 class="cert-title">Torvista Certified Solution Provider</h3>
    <p class="cert-text">It is a long established fact that a reader will be distracted by the readable content of a page when looking at its layout. The point of using Lorem Ipsum is that it has a more-or-less normal distribution of letters, as opposed to using , making it look like readable English.</p>
  </div>
</section>

<section class="services">
  <h2 class="section-title">What <strong>We Do</strong></h2>
  <p class="section-sub">Simply dummy text of the printing and typesetting industry.</p>
  <article class="service-card">
    <div class="service-icon"><svg width="40" height="36" viewBox="0 0 40 36" fill="none" stroke="#fff" stroke-width="2.5"><rect x="3" y="3" width="34" height="22" fill="#e8503a" stroke="#fff"/><path d="M14 32h12M20 25v7M16 11l-4 3 4 3M24 11l4 3-4 3"/></svg></div>
    <h3 class="service-name">Web Development</h3>
    <p class="service-text">It is a long established fact that a reader will be distracted by the readable content.</p>
    <a class="btn-small" href="#">Read More</a>
  </article>
  <article class="service-card">
    <div class="service-icon portrait" role="img" aria-label="Illustrated support agent with headset"></div>
    <h3 class="service-name">Web Support</h3>
    <p class="service-text">It is a long established fact that a reader will be distracted by the readable content.</p>
    <a class="btn-small" href="#">Read More</a>
  </article>
  <article class="service-card">
    <div class="service-icon"><svg width="40" height="40" viewBox="0 0 40 40" fill="none" stroke="#fff" stroke-width="4" stroke-linecap="round"><path d="M8 32 30 10M32 32 10 10"/><circle cx="31" cy="9" r="5" stroke-width="3"/></svg></div>
    <h3 class="service-name">Web Maintenance</h3>
    <p class="service-text">It is a long established fact that a reader will be distracted by the readable content.</p>
    <a class="btn-small" href="#">Read More</a>
  </article>
  <p class="services-note">High performance Torvista sites on time and on budget.</p>
  <a class="btn-ghost" href="#">Contact Us Now!</a>
</section>

<section class="testimonials">
  <h2 class="section-title">Client <strong>Testimonials</strong></h2>
  <p class="section-sub">What our Customers say About us and Reviews</p>
  <div class="client-photo" role="img" aria-label="Portrait photo of a smiling client in a suit and tie"></div>
  <div class="quote-rule"></div>
  <blockquote class="quote">" Lorem Ipsum is simply dummy text of the printing and typesetting industry. Lorem Ipsum has been the industry's standard dummy text ever since the 1500s, when an unknown printer took a galley of type and scrambled it to make a type specimen book. It has survived not only five centuries "</blockquote>
  <p class="quote-author">Harold Penwick, <span>USA</span></p>
</section>

<section class="portfolio">
  <h2 class="section-title">Our <strong>Portfolio</strong></h2>
  <p class="section-sub">Simply dummy text of the printing and typesetting industry.</p>
  <article class="project"><div class="project-shot shot-1" role="img" aria-label="Screenshot of a medical clinic website"></div><p class="project-name">Our project name 01</p></article>
  <article class="project"><div class="project-shot shot-2" role="img" aria-label="Screenshot of a creative design studio website"></div><p class="project-name">Our project name 02</p></article>
  <article class="project"><div class="project-shot shot-3" role="img" aria-label="Screenshot of a wedding website"></div><p class="project-name">Our project name 03</p></article>
  <article class="project"><div class="project-shot shot-4" role="img" aria-label="Screenshot of a travel website"></div><p class="project-name">Our project name 04</p></article>
  <a class="port-arrow prev" href="#" aria-label="Previous project"><svg width="20" height="60" viewBox="0 0 20 60"><path d="M18 2 2 30l16 28" fill="none" stroke="#666" stroke-width="2"/></svg></a>
  <a class="port-arrow next" href="#" aria-label="Next project"><svg width="20" height="60" viewBox="0 0 20 60"><path d="M2 2l16 28L2 58" fill="none" stroke="#666" stroke-width="2"/></svg></a>
  <a class="btn-view" href="#">View More</a>
</section>

<section class="tech-strip plain">
  <span class="tech-name">Markupa</span><span class="tech-name">Torvista</span><span class="tech-name">Brewlang</span><span class="tech-name">QRX</span><span class="tech-name">NCB</span><span class="tech-name">DataVane</span>
</section>

<footer class="site-footer">
  <div class="footer-col col-links">
    <h3>Quick Links</h3>
    <ul><li>- Home</li><li>- About Us</li><li>- Torvista</li><li>- Our Portfolio</li><li>- Contact Us</li></ul>
  </div>
  <div class="footer-col col-news">
    <h3>Sign Up Newsletter</h3>
    <p>Simply dummy text of the printing and typesetting industry.</p>
    <div class="news-field"><svg width="14" height="10" viewBox="0 0 14 10"><rect width="14" height="10" fill="#cccccc"/><path d="M0 0l7 5 7-5" fill="none" stroke="#3c3c3c"/></svg>Email Address</div>
    <div class="btn-submit">Submit</div>
  </div>
  <div class="footer-col col-contact">
    <h3>Contact Us</h3>
    <p>Suite 42, Level 3, 8 Wattlebrook Lane, Fernvale Heights VIC 3999</p>
    <p>Phone:<br>1300 648 907</p>
    <p>Email:<br>info@kavreo-commerce.example</p>
  </div>
  <div class="footer-map" role="img" aria-label="Grayscale street map showing the office location"></div>
  <a class="map-link" href="#">View Area Map</a>
</footer>
<div class="footer-base">Copyright © 2016 - Kavreo E-commerce, All Rights Reserved</div>

</body>
</html>
```